Business Card for my New Brokerage

Looking to get a business card design for my new Real Estate Brokerage.
I want it with Picture, Phone Number, Email, Website, Office Address
Name and Designation. Please add logo too.

Target Market(s)

Real Estate Investors or Home Buyers

Industry/Entity Type

Real Estate

Contact Information for Business Card

Name, Email, Phone Number, website, email, office address

Colors
EB3D1F
EC4F4E
F09395
F8D3D4
FCEDEE

Requirements
Must have
• Minimalistic, Clean, Modern, Photo
Nice to have
• White and Red Colors

```html
<!DOCTYPE html>
<html lang="en">
<head>
<meta charset="UTF-8">
<title>Ember Realty Inc – Business Card</title>
<link href="https://fonts.googleapis.com/css2?family=Lato:wght@400;900&display=swap" rel="stylesheet">
<style>
  :root{
    --stage:#2a2a2d;
    --card-dark:#1c1d20;
    --brand-red:#e00000;
    --gold:#d9b25a;
    --white:#ffffff;
    --rule:rgba(255,255,255,.55);
  }
  *{margin:0;padding:0;box-sizing:border-box}
  html,body{width:1200px;height:1108px;overflow:hidden;background:var(--stage)}
  body{font-family:'Lato',sans-serif;position:relative}
  .card{
    position:absolute;top:234px;width:400px;height:640px;border-radius:22px;overflow:hidden;
    background:var(--card-dark);box-shadow:0 14px 30px rgba(0,0,0,.45);
  }
  .card--front{left:150px}
  .card--back{left:650px}

  .portrait{
    position:absolute;left:0;top:0;width:400px;height:400px;
    background:radial-gradient(ellipse 55% 60% at 58% 48%, #5a4a42 0%, #34302f 45%, var(--card-dark) 80%);
  }
  .red-panel{position:absolute;left:0;top:0;width:400px;height:640px}

  .contact{position:absolute;left:0;right:0;top:398px;text-align:center;color:var(--white)}
  .contact__name{font-weight:900;font-size:30px;letter-spacing:.5px;text-transform:uppercase;line-height:1}
  .contact__title{font-weight:400;font-size:19px;margin-top:6px}
  .contact__icons{display:flex;align-items:center;justify-content:center;gap:8px;margin-top:14px}
  .contact__rule{width:80px;height:1px;background:var(--rule)}
  .icon{width:34px;height:34px;border-radius:6px;background:var(--white);display:flex;align-items:center;justify-content:center}
  .contact__lines{margin-top:12px;font-size:19px;line-height:31px}

  .brand{
    position:absolute;left:0;right:0;top:372px;text-align:center;color:var(--brand-red);font-weight:900;
  }
  .brand__name{font-size:54px;letter-spacing:2px;line-height:1}
  .brand__sub{font-size:15px;letter-spacing:5px;margin-top:4px}
</style>
</head>
<body>
  <section class="card card--front">
    <div class="portrait" role="img" aria-label="Portrait photo of the managing director in a dark suit and tie"></div>
    <svg class="red-panel" viewBox="0 0 400 640" aria-hidden="true">
      <path d="M0 250 Q 170 380 400 378 L400 640 L0 640 Z" fill="var(--brand-red)"/>
      <path d="M0 250 Q 170 380 400 378" fill="none" stroke="var(--gold)" stroke-width="4"/>
    </svg>
    <div class="contact">
      <p class="contact__name">Marcus Reed</p>
      <p class="contact__title">Managing Director</p>
      <div class="contact__icons">
        <span class="contact__rule"></span>
        <span class="icon"><svg width="20" height="20" viewBox="0 0 24 24"><path d="M6.6 10.8a15 15 0 0 0 6.6 6.6l2.2-2.2c.3-.3.7-.4 1-.2 1.1.4 2.3.6 3.6.6.6 0 1 .4 1 1V20c0 .6-.4 1-1 1A17 17 0 0 1 3 4c0-.6.4-1 1-1h3.5c.6 0 1 .4 1 1 0 1.3.2 2.5.6 3.6.1.3 0 .7-.2 1z" fill="var(--brand-red)"/></svg></span>
        <span class="icon"><svg width="22" height="22" viewBox="0 0 24 24"><rect x="3" y="5" width="18" height="14" rx="1.5" fill="none" stroke="var(--brand-red)" stroke-width="2"/><path d="M3 6l9 7 9-7M3 18l7-6M21 18l-7-6" fill="none" stroke="var(--brand-red)" stroke-width="2"/></svg></span>
        <span class="icon"><svg width="22" height="22" viewBox="0 0 24 24"><circle cx="12" cy="12" r="9" fill="none" stroke="var(--brand-red)" stroke-width="2"/><path d="M3 12h18M12 3c3 3 3 15 0 18M12 3c-3 3-3 15 0 18" fill="none" stroke="var(--brand-red)" stroke-width="1.6"/></svg></span>
        <span class="contact__rule"></span>
      </div>
      <div class="contact__lines">
        <p>055-210 874 316</p>
        <p>hello@emberhomes.com</p>
        <p>www.emberhomes.com</p>
      </div>
    </div>
  </section>

  <section class="card card--back">
    <div class="brand">
      <p class="brand__name">EMBER</p>
      <p class="brand__sub">REALTY INC</p>
    </div>
  </section>
</body>
</html>
```